Counseling Practice Business Card

I need a professional looking business card incorporating my new logo that was just completed. Card needs to incorporate my name and title, description of my specialty, my address, my phone number, my fax number, my email and my website URL. I need to be able to choose design on/with different paper colors and textures.
I do not have a lot of business card ideas so I am open to anything but I want bold,sharp, clear card without additional designs other than my logo (see attached file info). I am open to different color backgrounds or paper colors including black. I do not like traditional brackets around area codes in phone number or dashes between numbers in phone number. Am open to other ways of presenting including periods between numbers as appropriate. I do not know enough to know what I like yet but I want card to coordinate and work together with my logo. My practice emphasizes natural mental health interventions so any use of color (with background paper color or the blue and green in my logo) that elicits nature is nice. In addition to black, any natural brown or wood looking background might be desirable also. Most of the offerings so far look very similar and boring.

Target Market(s)

Potential therapy clients and other professionals

Contact Information for Business Card

Card information:
Gerald M. Whitcombe, Ph.D.
Licensed Clinical Psychologist
Integrative Health Coach
4812 Marlowe Ridge Blvd SE
Suite 310
Millbrook Glen, VT 05999
555 - 415-2983 phone
555 - 581-4096 fax
drgeraldwhitcombe@quillmarsh.net
brightfernwellness.net

Font styles to use
Serif
Sans Serif
Other font styles liked:
• anything that you think looks crisp, clear and easily readable

Requirements
Must have
• Any color used should coordinate with my logo design (see attached files).
• Card should be printed horizontally so top and bottom are longest sides of rectangle.
• Background color or paper color should complement and highlight logo. Do not like a white background. black, grey, brown or any color my logo would blend well with.
Nice to have
• I would like designer to utilize color to highlight letters/name or phone-fax-web symbols.
• Bottom edge of card could be highlighted if appropriate to an idea.
Should not have
• I would NOT want the card to have a pure white background at all.
• No clear cards.
• Cards should be oriented with long sides on bottom and top, NOT sides. DO NOT LIKE THIS THIN TALL ORIENTATION.

```html
<!DOCTYPE html>
<html lang="en">
<head>
<meta charset="utf-8">
<title>Brightfern Wellness – Business Cards</title>
<link href="https://fonts.googleapis.com/css2?family=Lato:wght@300;400;700;900&display=swap" rel="stylesheet">
<style>
  :root {
    --backdrop: #4a4b4d;
    --card: #131313;
    --brand-blue: #2a78c0;
    --brand-green: #1d7a3a;
    --text-light: #e8e8e8;
    --text-muted: #b9b9b9;
    --rule: #2b5d8f;
  }
  * { margin: 0; padding: 0; box-sizing: border-box; }
  html, body { width: 1200px; height: 1200px; overflow: hidden; }
  body {
    background: var(--backdrop);
    font-family: "Lato", sans-serif;
    position: relative;
  }
  .card {
    position: absolute;
    width: 760px;
    height: 434px;
    background: var(--card);
    border-radius: 30px;
    overflow: hidden;
    box-shadow: 0 18px 40px rgba(0,0,0,0.45);
  }
  .card--front { left: 110px; top: 140px; }
  .card--back { left: 330px; top: 620px; }

  .brand {
    display: flex;
    align-items: center;
    gap: 16px;
    color: var(--brand-blue);
    font-weight: 700;
    letter-spacing: 0.5px;
  }
  .brand__dot {
    width: 26px; height: 26px;
    border-radius: 50%;
    background: var(--brand-green);
    flex: none;
  }
  .brand__name { line-height: 1; }

  .card--front .brand {
    position: absolute;
    left: 0; right: 0; top: 140px;
    justify-content: center;
    font-size: 58px;
  }
  .front-web {
    position: absolute;
    left: 0; right: 0; bottom: 70px;
    display: flex;
    align-items: center;
    gap: 22px;
    color: var(--brand-blue);
    font-weight: 300;
    font-size: 26px;
    letter-spacing: 0.5px;
  }
  .front-web__rule { flex: 1; height: 1px; background: var(--rule); }

  .card--back .brand {
    position: absolute;
    left: 40px; top: 200px;
    font-size: 40px;
    width: 300px;
  }
  .card--back .brand__name { display: block; }
  .divider {
    position: absolute;
    left: 360px; top: 60px;
    width: 1px; height: 230px;
    background: #555;
  }
  .contact {
    position: absolute;
    left: 388px; top: 48px;
    right: 24px;
  }
  .contact__name {
    color: var(--brand-blue);
    font-weight: 900;
    font-size: 23px;
    text-transform: uppercase;
    letter-spacing: 0.2px;
  }
  .contact__name span { text-transform: none; }
  .contact__title {
    color: var(--text-light);
    font-weight: 300;
    font-size: 17px;
    line-height: 1.3;
  }
  .contact__list { list-style: none; margin-top: 14px; }
  .contact__item {
    display: flex;
    align-items: flex-start;
    gap: 12px;
    color: var(--text-light);
    font-size: 15.5px;
    line-height: 1.35;
    margin-bottom: 6px;
  }
  .contact__item--address { color: var(--text-muted); font-weight: 300; font-size: 14px; margin-bottom: 16px; }
  .contact__icon { width: 18px; height: 18px; flex: none; margin-top: 2px; }
  .band {
    position: absolute;
    left: 0; right: 0; bottom: 0;
    height: 44px;
    background: var(--brand-blue);
  }
</style>
</head>
<body>

<section class="card card--front" aria-label="Card front">
  <div class="brand">
    <span class="brand__dot"></span>
    <span class="brand__name">Brightfern Wellness</span>
  </div>
  <div class="front-web">
    <span class="front-web__rule"></span>
    <span>www.brightfernwellness.net</span>
    <span class="front-web__rule"></span>
  </div>
</section>

<section class="card card--back" aria-label="Card back">
  <div class="brand">
    <span class="brand__dot"></span>
    <span class="brand__name">Brightfern<br>Wellness</span>
  </div>
  <div class="divider"></div>
  <div class="contact">
    <p class="contact__name">Gerald M. Whitcombe, <span>Ph.D.</span></p>
    <p class="contact__title">Licensed Clinical Psychologist<br>Integrative Health Coach</p>
    <ul class="contact__list">
      <li class="contact__item contact__item--address">
        <svg class="contact__icon" viewBox="0 0 24 24"><path d="M12 2a7 7 0 0 0-7 7c0 5 7 13 7 13s7-8 7-13a7 7 0 0 0-7-7z" fill="var(--brand-blue)"/><circle cx="12" cy="9" r="2.6" fill="var(--card)"/></svg>
        <span>4812 Marlowe Ridge Blvd SE, Suite 310<br>Millbrook Glen, VT 05999</span>
      </li>
      <li class="contact__item">
        <svg class="contact__icon" viewBox="0 0 24 24"><path d="M6.6 10.8a15 15 0 0 0 6.6 6.6l2.2-2.2a1 1 0 0 1 1-.25 11 11 0 0 0 3.6.57 1 1 0 0 1 1 1V20a1 1 0 0 1-1 1A17 17 0 0 1 3 4a1 1 0 0 1 1-1h3.5a1 1 0 0 1 1 1c0 1.25.2 2.450.57 3.6a1 1 0 0 1-.25 1z" fill="var(--brand-blue)"/></svg>
        <span>555 - 415-2983</span>
      </li>
      <li class="contact__item">
        <svg class="contact__icon" viewBox="0 0 24 24" fill="none" stroke="var(--brand-blue)" stroke-width="1.6"><rect x="4" y="9" width="16" height="10" rx="1"/><path d="M7 9V4h10v5M8 13h8M8 16h5"/></svg>
        <span>555 - 581-4096</span>
      </li>
      <li class="contact__item">
        <svg class="contact__icon" viewBox="0 0 24 24" fill="none" stroke="var(--brand-blue)" stroke-width="1.6"><rect x="3" y="5" width="18" height="14" rx="1"/><path d="M3 6l9 7 9-7"/></svg>
        <span>drgeraldwhitcombe@quillmarsh.net</span>
      </li>
      <li class="contact__item">
        <svg class="contact__icon" viewBox="0 0 24 24" fill="none" stroke="var(--brand-blue)" stroke-width="1.6"><circle cx="12" cy="12" r="9"/><ellipse cx="12" cy="12" rx="4" ry="9"/><path d="M3 12h18M5 7h14M5 17h14"/></svg>
        <span>www.brightfernwellness.net</span>
      </li>
    </ul>
  </div>
  <div class="band"></div>
</section>

</body>
</html>
```